Website for International Non-Profit for Birth Parent Searching

LumaKin is a 501(c)(3) non-profit organization that helps Chinese adoptees search and reunite with birth families who were separated due the One Child Policy in China. We want to create a website that can link to an information database that allows website users to easily access information around search ads in an organized way; help connect families to professional searchers; provide resources for community support for adoptees and their families as they embark on a personal and emotional journey of finding birth family through support groups on social media and consultation/education on the searching process; and provide the opportunity for the adoptive community to give back through donations and volunteer opportunities. The final design should foster a sense of community and be easy navigable to access the multiple resources we provide to help families search for each other. We would like to see designs with red/black/white color schemes that are gentle, inviting, and family friendly to viewers. We would like to see some design layouts with Chinese themes, if possible.

```html
<!DOCTYPE html>
<html lang="en">
<head>
<meta charset="utf-8">
<title>LumaKin — Reuniting Families</title>
<link href="https://fonts.googleapis.com/css2?family=Cinzel:wght@400;600;700&family=Montserrat:wght@700&family=Roboto:wght@400;500;700&display=swap" rel="stylesheet">
<style>
:root{
  --red:#d10d0d;
  --red-dark:#b50a0a;
  --black:#111111;
  --ink:#222222;
  --grey:#6e6e6e;
  --light:#f4f4f4;
  --white:#ffffff;
  --dark-band:#1c1c1c;
}
*{box-sizing:border-box;margin:0;padding:0}
html,body{width:1200px;height:3950px;overflow:hidden}
body{font-family:'Roboto',Arial,sans-serif;color:var(--ink);background:var(--white);position:relative}
.abs{position:absolute}
.serif{font-family:'Cinzel',Georgia,serif}
.red{color:var(--red)}
.btn{position:absolute;display:flex;align-items:center;justify-content:center;gap:8px;border-radius:30px;font-weight:700;font-size:15px;color:var(--white);text-transform:uppercase}
.btn svg{width:14px;height:14px}
.btn-red{background:var(--red)}
.btn-black{background:var(--black)}

/* header */
.header{top:0;left:0;width:1200px;height:92px;background:var(--white)}
.logo{font-family:'Cinzel',Georgia,serif;font-size:25px;font-weight:600;color:var(--red);letter-spacing:1px}
.call{left:540px;top:20px;display:flex;align-items:center;gap:14px}
.call small{display:block;font-size:12px;color:var(--ink)}
.call strong{font-size:21px;font-weight:700;letter-spacing:.5px}
.nav{top:92px;left:0;width:1200px;height:43px;background:var(--red);display:flex;justify-content:center;align-items:center;gap:38px}
.nav a{color:var(--white);font-size:15px;font-weight:700;text-decoration:none}

/* hero */
.hero{top:135px;left:0;width:1200px;height:616px;background:linear-gradient(135deg,#5f7a2d 0%,#9bb256 40%,#d9a08a 55%,#7d9c3e 75%,#4b6520 100%)}
.hero h1{left:110px;top:180px;font-family:'Cinzel',Georgia,serif;font-size:58px;font-weight:600;color:var(--white)}
.hero p{left:112px;top:265px;width:420px;font-size:16px;font-weight:500;line-height:27px;color:var(--white)}

.feature{width:108px;height:108px;border-radius:50%;background:var(--white);display:flex;align-items:center;justify-content:center;top:696px}
.feature .inner{width:88px;height:88px;border-radius:50%;display:flex;align-items:center;justify-content:center;border:5px solid var(--white);box-shadow:0 0 0 3px var(--black)}
.feature.mid .inner{background:var(--red);box-shadow:0 0 0 3px var(--red)}
.feature .inner{background:var(--black)}
.feature-text{top:820px;font-size:14px;line-height:26px;text-align:center;color:var(--ink)}

/* about */
.about-photo{left:112px;top:1048px;width:422px;height:368px;background:linear-gradient(160deg,#8fb35a,#c9d9a8 45%,#6c9a36);border-radius:70px 0 70px 0}
.section-title{font-family:'Cinzel',Georgia,serif;font-weight:700;color:var(--black)}
.about h2{left:600px;top:1055px;font-size:48px}
.body-text{font-size:14px;line-height:26px;color:var(--grey)}

/* kindness band */
.band{top:1534px;left:0;width:1200px;height:291px;background:var(--red);overflow:hidden}
.band-photo{left:655px;top:-40px;width:700px;height:380px;border-radius:50%;background:linear-gradient(120deg,#7b9a3c,#e07a2a 45%,#a8c26a);border:4px solid var(--white)}
.band h2{left:112px;top:42px;font-size:28px;line-height:32px;color:var(--white);font-weight:700}
.band p{left:112px;top:126px;width:520px;font-size:14px;line-height:24px;color:var(--white)}

/* stories */
.stories h2{left:0;width:1200px;top:1908px;text-align:center;font-size:46px}
.card{top:1993px;width:308px;height:387px;background:var(--white);border-radius:10px;box-shadow:0 4px 18px rgba(0,0,0,.08);text-align:center}
.card .img{margin:7px;height:204px;border-radius:6px}
.card h3{font-size:17px;font-weight:700;margin-top:30px;color:var(--black)}
.card p{font-size:14px;line-height:23px;color:var(--grey);margin:14px 20px 0}
.card .more{display:inline-flex;align-items:center;gap:6px;margin-top:14px;color:var(--red);font-weight:700;font-size:14px}
.card .more svg{width:13px;height:13px}

/* gallery */
.gallery h2{left:0;width:1200px;top:2456px;text-align:center;font-size:46px}
.g{position:absolute}

/* contact */
.contact{top:3065px;left:0;width:1200px;height:605px;background:linear-gradient(180deg,#161616,#2a2a2a 60%,#1a1a1a)}
.contact h2{left:0;width:1200px;top:60px;text-align:center;font-family:'Montserrat',Arial,sans-serif;font-size:40px;color:var(--white);letter-spacing:1px}
.contact .rule{left:548px;top:115px;width:104px;height:4px;background:var(--white);border-radius:2px}
.field{position:absolute;background:var(--white);font-size:14px;color:var(--grey);padding:20px 22px}

/* footer */
.footer-links{left:362px;top:3732px;display:flex;gap:14px;font-size:15px;color:var(--grey)}
.social{top:3728px;width:34px;height:34px;border-radius:50%;border:1px solid #cfcfcf;background:var(--white)}
.foot-item{top:3792px;display:flex;gap:12px}
.foot-item .pin{width:30px;height:30px;border-radius:50%;background:var(--red);display:flex;align-items:center;justify-content:center;flex:none}
.foot-item .pin svg{width:15px;height:15px}
.foot-item b{font-size:15px;font-weight:500;color:var(--black);display:block}
.foot-item span{font-size:13px;color:var(--grey);line-height:19px}
.copyright{top:3912px;left:0;width:1200px;text-align:center;font-size:15px;color:var(--grey)}
</style>
</head>
<body>

<!-- header -->
<header class="abs header">
  <div class="abs logo" style="left:110px;top:28px">LumaKin</div>
  <div class="abs call">
    <svg width="30" height="30" viewBox="0 0 24 24"><path fill="#d10d0d" d="M6.6 10.8a15.1 15.1 0 0 0 6.6 6.6l2.2-2.2c.3-.3.7-.4 1-.2 1.1.4 2.3.6 3.6.6.6 0 1 .4 1 1V20c0 .6-.4 1-1 1A17 17 0 0 1 3 4c0-.6.4-1 1-1h3.5c.6 0 1 .4 1 1 0 1.3.2 2.5.6 3.6.1.3 0 .7-.2 1z"/></svg>
    <div><small>Call Us</small><strong>(555) 014-2730</strong></div>
  </div>
  <div class="btn btn-black" style="left:790px;top:26px;width:142px;height:40px;font-size:14px">Serach Ads</div>
  <div class="btn btn-red" style="left:945px;top:26px;width:142px;height:40px;font-size:14px">Serach Ads</div>
</header>
<nav class="abs nav">
  <a>HOME</a><a>ABOUT US</a><a>OUR ORGANIZE</a><a>PROJECTS</a><a>GALLERIES</a><a>NEWSLETTERS</a><a>CONTACT US</a>
</nav>

<!-- hero -->
<section class="abs hero" role="img" aria-label="Photo of a smiling family lying together on the grass in a park">
  <h1 class="abs">LumaKin</h1>
  <p class="abs">Lorem ipsum dolor sit amet, adipiscing elit, sed do eiusmod tempor incididunt ut labore</p>
  <div class="btn btn-red" style="left:112px;top:342px;width:188px;height:47px">Get Started
    <svg viewBox="0 0 16 16"><circle cx="8" cy="8" r="8" fill="#fff"/><path d="M6.5 4.5 10 8l-3.5 3.5" stroke="#d10d0d" stroke-width="2" fill="none"/></svg></div>
</section>

<!-- features -->
<div class="abs feature" style="left:176px"><div class="inner">
  <svg width="44" height="44" viewBox="0 0 44 44" fill="none" stroke="#fff" stroke-width="3"><circle cx="19" cy="19" r="11"/><path d="M27 27l10 10"/><circle cx="19" cy="19" r="5"/></svg></div></div>
<div class="abs feature mid" style="left:546px"><div class="inner">
  <svg width="46" height="46" viewBox="0 0 46 46" fill="none" stroke="#fff" stroke-width="2.5"><circle cx="15" cy="14" r="6"/><circle cx="31" cy="14" r="6"/><path d="M5 38v-8a8 8 0 0 1 8-8h4a8 8 0 0 1 8 8v8M21 38v-8a8 8 0 0 1 8-8h4a8 8 0 0 1 8 8v8"/></svg></div></div>
<div class="abs feature" style="left:914px"><div class="inner">
  <svg width="46" height="46" viewBox="0 0 46 46" fill="none" stroke="#fff" stroke-width="2.5"><path d="M23 26s-9-6-9-12a5 5 0 0 1 9-2 5 5 0 0 1 9 2c0 6-9 12-9 12z"/><path d="M5 24l8 12h10M41 24l-8 12H23"/></svg></div></div>

<p class="abs feature-text" style="left:100px;width:270px">Help connect families to professional searchers</p>
<p class="abs feature-text" style="left:410px;width:380px">provide resources for community support for adoptees and their families as they embark on a personal and emotional journey of finding birth family through support groups on social media and consultation/education on the searching process</p>
<p class="abs feature-text" style="left:850px;width:240px">provide the opportunity for the adoptive community to give back through donations and volunteer opportunities</p>

<!-- about -->
<section class="about">
  <div class="abs about-photo" role="img" aria-label="Photo of a grandfather, mother and children running across a lawn"></div>
  <h2 class="abs section-title">About <span class="red">Us</span></h2>
  <p class="abs body-text" style="left:600px;top:1132px;width:490px">Lorem ipsum dolor sit amet, consectetur adipiscing elit, sed do eiusmod tempor incididunt ut labore et dolore magna aliqua. Ut enim ad minim veniam, quis nostrud exercitation ullamco laboris nisi ut aliquip ex ea commodo consequat.</p>
  <p class="abs body-text" style="left:600px;top:1242px;width:490px">Sed ut perspiciatis unde omnis iste natus error sit voluptatem accusantium doloremque laudantium, totam rem aperiam, eaque ipsa quae ab illo inventore veritatis et dicta sunt explicabo.</p>
  <div class="btn btn-red" style="left:600px;top:1352px;width:170px;height:45px;font-size:14px">Read More
    <svg viewBox="0 0 16 16"><circle cx="8" cy="8" r="8" fill="#fff"/><path d="M6.5 4.5 10 8l-3.5 3.5" stroke="#d10d0d" stroke-width="2" fill="none"/></svg></div>
</section>

<!-- kindness band -->
<section class="abs band">
  <div class="abs band-photo" role="img" aria-label="Photo of children in colourful costumes running outdoors"></div>
  <h2 class="abs serif">Your kindness can give these<br>children future</h2>
  <p class="abs">Sed ut perspiciatis unde omnis iste natus error sit voluptatem accusantium doloremque laudantium, totam rem aperiam,sunt explicabo.</p>
  <div class="btn btn-black" style="left:112px;top:197px;width:160px;height:43px;font-size:14px">Donate
    <svg viewBox="0 0 16 16"><circle cx="8" cy="8" r="8" fill="#fff"/><path d="M6.5 4.5 10 8l-3.5 3.5" stroke="#111" stroke-width="2" fill="none"/></svg></div>
</section>

<!-- stories -->
<section class="stories">
  <h2 class="abs section-title">Featured <span class="red">Stories</span></h2>
  <article class="abs card" style="left:112px">
    <div class="img" role="img" aria-label="Photo of a family blowing bubbles on the grass" style="background:linear-gradient(180deg,#a8c27a,#6f9a3a)"></div>
    <h3>Lorem ipsum dolor sit amet</h3>
    <p>Sed ut perspiciatis unde omnis iste natus error sit voluptatem accusantium</p>
    <span class="more">READ MORE <svg viewBox="0 0 16 16"><circle cx="8" cy="8" r="8" fill="#d10d0d"/><path d="M6.5 4.5 10 8l-3.5 3.5" stroke="#fff" stroke-width="2" fill="none"/></svg></span>
  </article>
  <article class="abs card" style="left:446px">
    <div class="img" role="img" aria-label="Photo of children sitting in a circle on a lawn" style="background:linear-gradient(180deg,#8fae4a,#4f7a22)"></div>
    <h3>Lorem ipsum dolor sit amet</h3>
    <p>Sed ut perspiciatis unde omnis iste natus error sit voluptatem accusantium</p>
    <span class="more">READ MORE <svg viewBox="0 0 16 16"><circle cx="8" cy="8" r="8" fill="#d10d0d"/><path d="M6.5 4.5 10 8l-3.5 3.5" stroke="#fff" stroke-width="2" fill="none"/></svg></span>
  </article>
  <article class="abs card" style="left:780px">
    <div class="img" role="img" aria-label="Photo of a smiling family posing together outdoors" style="background:linear-gradient(135deg,#7f9b4a,#e8a0a0 55%,#6b8a3a)"></div>
    <h3>Lorem ipsum dolor sit amet</h3>
    <p>Sed ut perspiciatis unde omnis iste natus error sit voluptatem accusantium</p>
    <span class="more">READ MORE <svg viewBox="0 0 16 16"><circle cx="8" cy="8" r="8" fill="#d10d0d"/><path d="M6.5 4.5 10 8l-3.5 3.5" stroke="#fff" stroke-width="2" fill="none"/></svg></span>
  </article>
</section>

<!-- gallery -->
<section class="gallery">
  <h2 class="abs section-title"><span class="red">Our</span> Gallery</h2>
  <div class="g" role="img" aria-label="Photo of parents and daughter laughing on a sofa" style="left:112px;top:2550px;width:488px;height:413px;background:linear-gradient(135deg,#e4e2de,#c9c3bb 60%,#8a8f9a)"></div>
  <div class="g" role="img" aria-label="Photo of a father hugging his daughters" style="left:617px;top:2550px;width:228px;height:172px;background:linear-gradient(135deg,#9bb070,#c8c2b5)"></div>
  <div class="g" role="img" aria-label="Photo of children using a laptop together" style="left:617px;top:2733px;width:228px;height:230px;background:linear-gradient(135deg,#f0ede8,#e08a3a 50%,#3f8fd0)"></div>
  <div class="g" role="img" aria-label="Photo of a father carrying his child on his shoulders at the beach" style="left:862px;top:2550px;width:226px;height:231px;background:linear-gradient(180deg,#f1e6da,#d8c5b0)"></div>
  <div class="g" role="img" aria-label="Photo of three children sitting on a couch" style="left:862px;top:2792px;width:226px;height:171px;background:linear-gradient(180deg,#cfc8bf,#5a4f46)"></div>
</section>

<!-- contact -->
<section class="abs contact" role="img" aria-label="Dark background photo of a family">
  <h2 class="abs">CONTACT US</h2>
  <div class="abs rule"></div>
  <div class="field" style="left:177px;top:170px;width:413px;height:55px">Name</div>
  <div class="field" style="left:610px;top:170px;width:413px;height:55px">Email</div>
  <div class="field" style="left:177px;top:242px;width:413px;height:55px">Phone</div>
  <div class="field" style="left:610px;top:242px;width:413px;height:55px">Company</div>
  <div class="field" style="left:177px;top:315px;width:846px;height:126px">Message</div>
  <div class="btn btn-red" style="left:514px;top:487px;width:172px;height:50px;font-size:19px;text-transform:uppercase">Submit</div>
</section>

<!-- footer -->
<footer>
  <div class="abs logo" style="left:110px;top:3765px;font-size:32px">LumaKin</div>
  <div class="abs footer-links"><span>Home</span><span>|</span><span>About Us</span><span>|</span><span>Our Organize</span><span>|</span><span>Galleries</span><span>|</span><span>Newsletters</span><span>|</span><span>Contact</span></div>
  <div class="abs social" style="left:955px"></div>
  <div class="abs social" style="left:1003px"></div>
  <div class="abs social" style="left:1051px"></div>
  <div class="abs" style="left:362px;top:3775px;width:726px;height:1px;background:#e2e2e2"></div>
  <div class="abs foot-item" style="left:358px">
    <div class="pin"><svg viewBox="0 0 24 24"><path fill="#fff" d="M12 2a7 7 0 0 0-7 7c0 5 7 13 7 13s7-8 7-13a7 7 0 0 0-7-7zm0 9.5A2.5 2.5 0 1 1 12 6.5a2.5 2.5 0 0 1 0 5z"/></svg></div>
    <div><b>Address</b><span>Lotus Lane 42,<br>Harbor City</span></div>
  </div>
  <div class="abs foot-item" style="left:638px">
    <div class="pin"><svg viewBox="0 0 24 24"><path fill="#fff" d="M6.6 10.8a15.1 15.1 0 0 0 6.6 6.6l2.2-2.2c.3-.3.7-.4 1-.2 1.1.4 2.3.6 3.6.6.6 0 1 .4 1 1V20c0 .6-.4 1-1 1A17 17 0 0 1 3 4c0-.6.4-1 1-1h3.5c.6 0 1 .4 1 1 0 1.3.2 2.5.6 3.6.1.3 0 .7-.2 1z"/></svg></div>
    <div><b>Phone</b><span>(555) 014- 2730</span></div>
  </div>
  <div class="abs foot-item" style="left:842px">
    <div class="pin"><svg viewBox="0 0 24 24"><path fill="#fff" d="M3 6h18v12H3z"/><path d="M3 6l9 7 9-7" stroke="#d10d0d" stroke-width="2" fill="none"/></svg></div>
    <div><b>Email</b><span>hello@lumakin.org</span></div>
  </div>
  <div class="abs" style="left:112px;top:3888px;width:976px;height:1px;background:#e2e2e2"></div>
  <p class="abs copyright">© 2021 LumaKin. All Rights Reserved &nbsp; | &nbsp; Privacy Policy &nbsp; | &nbsp; Terms &amp; Condition</p>
</footer>

</body>
</html>
```